Media Services Start-up -- Corporate Website and Logo Design. Inspiration required!

We need a logo design and corporate website design, including coding, for our start-up business.
Vennatra’s value proposition is based on bringing together media content from a vast number of geographies globally, adding human and AI curation, translation and editing, and delivering the content using tailored customer interfaces. On the one hand, the business brings together media coverage from all over the world, and on the other it brings together content, human skills and technology to deliver a supreme customer experience.
Vennatra is a B2B media monitoring and analytics business with emphasis on global customers. Vennatra's service offering is centred around sourcing media content from different markets, processing, storing and delivering the content and insights derived from it using an online platform / mobile app.
The messaging we want to create through the logo is:
- Global scope
- Speed of delivery
- Cost-efficiency
- Multi-lingual
- Tailor-made
- Trustworthy
Target Market(s)
Business to business, PR / Communications, Media, Marketing
Logo Text
Vennatra
Coding
Coded - Design and coding required
Number of Pages Required
5+ page
Font styles to use
Other font styles liked:
- See Design Brief for details
Colors
Designer to choose colors to be used in the design.

```html
<!DOCTYPE html>
<html lang="en">
<head>
<meta charset="utf-8">
<title>How We Do It — Vennatra</title>
<link href="https://fonts.googleapis.com/css2?family=Questrial&family=Josefin+Sans:wght@100;200&display=swap" rel="stylesheet">
<style>
:root{
  --sky:#64b1ee;
  --sky-deep:#4f9ad8;
  --navy:#07133a;
  --accent:#5cc9f5;
  --orange:#f47421;
  --ink:#3a3a3a;
  --text:#4a4a4a;
  --muted:#9a9a9a;
  --line-faint:#e7eef5;
  --placeholder:#f0f0f0;
  --sand:#f3efec;
  --white:#ffffff;
}
*{box-sizing:border-box;margin:0;padding:0}
html,body{width:1200px;height:2731px;overflow:hidden}
body{position:relative;background:var(--white);font-family:"Questrial",sans-serif;color:var(--text)}
.abs{position:absolute}

/* Header */
.hero-band{left:0;top:0;width:1200px;height:300px}
.topbar-call{left:700px;top:14px;width:219px;text-align:right;font-size:10px;color:var(--white)}
.topbar-btn{left:932px;top:8px;width:98px;height:25px;background:var(--orange);color:var(--white);font-size:10px;display:flex;align-items:center;justify-content:center;gap:4px;border-radius:2px}
.nav{top:58px;font-size:11.5px;color:var(--white)}
.hero-title{left:0;top:158px;width:1200px;text-align:center;font-size:37px;color:var(--white)}

/* Timeline */
.spine{left:599px;width:2px}
.spine.faint{background:var(--line-faint)}
.spine.bold{background:var(--accent)}
.node{width:32px;height:32px;border-radius:50%;background:var(--accent);left:584px;display:flex;align-items:center;justify-content:center;box-shadow:0 0 0 4px var(--white)}
.node i{width:10px;height:10px;background:var(--white);border-radius:50%;display:block}
.node i.square{border-radius:1px}
.step-num{font-family:"Josefin Sans",sans-serif;font-weight:100;font-size:150px;line-height:1;color:var(--accent)}

.card{background:var(--white);box-shadow:0 2px 14px rgba(0,0,0,.06);width:561px;height:592px}
.card-media{position:absolute;left:0;top:0;width:402px;height:402px;background:var(--placeholder)}
.card-media.globe{border-radius:50%;background:radial-gradient(circle at 45% 45%,#7cbef2,var(--sky) 70%)}
.card-title{position:absolute;left:31px;top:444px;font-size:18px;color:var(--ink);letter-spacing:.2px}
.card-body{position:absolute;left:31px;top:483px;width:505px;font-size:13px;line-height:19.3px;color:var(--text)}

/* CTA */
.cta{left:0;top:2217px;width:1200px;height:201px;background:var(--sand)}
.cta-title{left:0;top:2253px;width:1200px;text-align:center;font-size:44px;color:#111}
.field{top:2318px;width:166px;height:37px;border:1px solid #cfcfcf;background:var(--white);font-size:12px;color:var(--muted);padding:12px 12px}
.cta-btn{left:786px;top:2318px;width:166px;height:37px;background:var(--orange);color:var(--white);font-size:12px;font-weight:bold;display:flex;align-items:center;justify-content:center}

/* Footer */
.footer{left:0;top:2418px;width:1200px;height:313px;background:var(--navy)}
.foot-head{top:2452px;font-size:11px;color:#2aa6f0;letter-spacing:.3px}
.foot-list{top:2489px;font-size:13px;line-height:23.5px;color:var(--white);list-style:none}
.foot-list li{display:flex;align-items:center;gap:4px}
.foot-rule{left:170px;top:2670px;width:860px;height:1px;background:#25305a}
.copyright{left:0;top:2688px;width:1200px;text-align:center;font-size:10px;color:var(--white);font-weight:bold}
</style>
</head>
<body>

<!-- Header band -->
<svg class="abs hero-band" viewBox="0 0 1200 300" aria-hidden="true">
  <defs>
    <linearGradient id="bandShade" x1="0" y1="0" x2="1" y2="1">
      <stop offset="0" stop-color="#64b1ee"/>
      <stop offset=".72" stop-color="#5fa9e6"/>
      <stop offset="1" stop-color="#1c3d66"/>
    </linearGradient>
  </defs>
  <polygon points="0,0 1200,0 1200,295 0,222" fill="url(#bandShade)"/>
</svg>
<div class="abs topbar-call">Call us on: +(00) 05 5550 1920</div>
<div class="abs topbar-btn">Learn more
  <svg width="9" height="9" viewBox="0 0 10 10"><circle cx="5" cy="5" r="4" fill="none" stroke="#fff" stroke-width="1.2"/><path d="M4 3l2 2-2 2" fill="none" stroke="#fff" stroke-width="1.2"/></svg>
</div>
<nav>
  <span class="abs nav" style="left:584px">Home</span>
  <span class="abs nav" style="left:647px">Solutions</span>
  <span class="abs nav" style="left:728px">How We Do It</span>
  <span class="abs nav" style="left:835px">Our People</span>
  <span class="abs nav" style="left:927px">Our Technology</span>
</nav>
<h1 class="abs hero-title" style="font-weight:normal">How we process and deliver solutions</h1>

<!-- Timeline spine -->
<div class="abs spine bold" style="top:602px;height:193px"></div>
<div class="abs spine faint" style="top:795px;height:245px"></div>
<div class="abs spine bold" style="top:1040px;height:275px"></div>
<div class="abs spine faint" style="top:1315px;height:245px"></div>
<div class="abs spine bold" style="top:1560px;height:274px"></div>

<div class="abs node" style="top:586px"><i></i></div>
<div class="abs node" style="top:1202px"><i></i></div>
<div class="abs node" style="top:1818px"><i class="square"></i></div>

<div class="abs step-num" style="left:632px;top:545px">1</div>
<div class="abs step-num" style="left:482px;top:1160px">2</div>
<div class="abs step-num" style="left:628px;top:1778px">3</div>

<!-- Step 1 -->
<article class="abs card" style="left:8px;top:307px">
  <div class="card-media globe" role="img" aria-label="Illustration of the globe showing the continents"></div>
  <h3 class="card-title" style="font-weight:normal">How we do it #1</h3>
  <p class="card-body">Lorem ipsum dolor sit amet, mea ei viderer probatus consequuntur, sonet vocibus lobortis has ad. Eos erant indoctum an, dictas invidunt est ex, et sea consulatu torquatos. Nostro aperiam petentium eu nam, mel debet urbanitas ad, idque complectitur eu quo. An sea autem dolore dolores.</p>
</article>

<!-- Step 2 -->
<article class="abs card" style="left:631px;top:921px">
  <div class="card-media" role="img" aria-label="Image placeholder for step two"></div>
  <h3 class="card-title" style="font-weight:normal">How we do it #2</h3>
  <p class="card-body">Lorem ipsum dolor sit amet, mea ei viderer probatus consequuntur, sonet vocibus lobortis has ad. Eos erant indoctum an, dictas invidunt est ex, et sea consulatu torquatos. Nostro aperiam petentium eu nam, mel debet urbanitas ad, idque complectitur eu quo. An sea autem dolore dolores.</p>
</article>

<!-- Step 3 -->
<article class="abs card" style="left:8px;top:1538px">
  <div class="card-media" role="img" aria-label="Image placeholder for step three"></div>
  <h3 class="card-title" style="font-weight:normal">How we do it #3</h3>
  <p class="card-body">Lorem ipsum dolor sit amet, mea ei viderer probatus consequuntur, sonet vocibus lobortis has ad. Eos erant indoctum an, dictas invidunt est ex, et sea consulatu torquatos. Nostro aperiam petentium eu nam, mel debet urbanitas ad, idque complectitur eu quo. An sea autem dolore dolores.</p>
</article>

<!-- Call to action -->
<section class="abs cta"></section>
<h2 class="abs cta-title" style="font-weight:normal">Learn more about Vennatra</h2>
<div class="abs field" style="left:249px">Name</div>
<div class="abs field" style="left:427px">Email</div>
<div class="abs field" style="left:606px">Phone</div>
<div class="abs cta-btn">GET STARTED</div>

<!-- Footer -->
<footer class="abs footer"></footer>
<div class="abs foot-head" style="left:170px">VENNATRA</div>
<div class="abs foot-head" style="left:467px">SOLUTIONS</div>
<div class="abs foot-head" style="left:764px">OUR TECHNOLOGY</div>

<ul class="abs foot-list" style="left:170px">
  <li><svg width="9" height="12" viewBox="0 0 9 12"><path d="M4.5 0A4.5 4.5 0 0 0 0 4.5C0 8 4.5 12 4.5 12S9 8 9 4.5A4.5 4.5 0 0 0 4.5 0zm0 6.3a1.8 1.8 0 1 1 0-3.6 1.8 1.8 0 0 1 0 3.6z" fill="#fff"/></svg>48 Harrow Lane, Fairmont, NS 20417.</li>
  <li><svg width="11" height="11" viewBox="0 0 12 12"><path d="M2.5 0.5l2 2.5-1.2 1.3c.7 1.6 2 2.9 3.5 3.6l1.3-1.2 2.5 2-1 2.3C5.5 11 1 6.5 0.3 1.5z" fill="#fff"/></svg>555.010203</li>
  <li><svg width="12" height="10" viewBox="0 0 12 10"><rect x=".6" y=".6" width="10.8" height="8.8" rx="1" fill="none" stroke="#fff" stroke-width="1.2"/><path d="M1 1.5l5 4 5-4" fill="none" stroke="#fff" stroke-width="1.2"/></svg>hello@vennatra.com</li>
</ul>
<ul class="abs foot-list" style="left:467px">
  <li>Content Sourcing</li>
  <li>Content Collection</li>
  <li>Content Augmentation</li>
  <li>Content Delivery</li>
  <li>Media Insights &amp; Consultancy</li>
</ul>
<ul class="abs foot-list" style="left:764px;width:240px">
  <li style="display:block;line-height:19.5px;margin-bottom:4px">Content Ingestion / Normalisation &amp; Augmentation</li>
  <li>Content Delivery</li>
  <li>Insight Services</li>
</ul>
<div class="abs foot-rule"></div>
<div class="abs copyright">© 2019 Vennatra</div>

</body>
</html>
```